A5 Flyer for Financial Services Business

I am after a re-design of our business flyer to fit in with our new branding style and logo colour scheme. Wanting something with a bit of designer flair that I could not create myself. I have included the flyer which I created which lacks style so dazzle me.

I want to use the same content.

Text for main body of flyer is

Are you a small business owner, tradie or TRPQ Service Provider struggling to stay on top of your bookkeeping and compliance obligations? If so we would love to help you get back on track and take control of your business finances so that you can make informed business decisions and focus on what you do best.

We have over 20 years industry experience and, as a small business ourselves, we are able to offer our clients a personal bookkeeping solution tailored to meet the needs of your business.

Accounts Payable | Accounts Receivable
Customer Invoicing
Bank and Credit Card Reconciliations
Payroll | Superannuation | Payroll Tax
Business Activity | Instalment Activity Statements
Regular Financial Reports
Vantly and Brimfolk Set-Up and Training

```html
<!DOCTYPE html>
<html lang="en">
<head>
<meta charset="utf-8">
<title>Steady Ledger Bookkeeping – Flyer</title>
<link rel="stylesheet" href="https://fonts.googleapis.com/css2?family=Montserrat:wght@400;600;700;800;900&family=Open+Sans:wght@400;600;700&display=swap">
<style>
  :root {
    --teal: #1b9ea6;
    --teal-light: #2bb7bd;
    --teal-dark: #0e5a66;
    --navy: #0b3d49;
    --grey: #5d6265;
    --grey-light: #d7dadb;
    --grey-mid: #9aa0a3;
    --white: #ffffff;
    --ink: #3b3f42;
  }
  * { margin: 0; padding: 0; box-sizing: border-box; }
  html, body { width: 784px; height: 1200px; overflow: hidden; background: var(--white); }
  .flyer {
    position: relative; width: 784px; height: 1200px; overflow: hidden;
    background: var(--white); font-family: "Open Sans", Arial, sans-serif; color: var(--ink);
  }
  .hero-photo {
    position: absolute; left: 380px; top: 0; width: 404px; height: 340px;
    background: linear-gradient(135deg, #eef3f5 0%, #c9d6dc 45%, #3b4d5e 100%);
    clip-path: polygon(90px 0, 100% 0, 100% 100%, 0 100%);
  }
  .hero-frame { position: absolute; left: 300px; top: 0; }
  .brand {
    position: absolute; left: 40px; top: 40px; display: flex; align-items: center; gap: 12px;
  }
  .brand-mark { width: 44px; height: 44px; border-radius: 50%; background: var(--teal); }
  .brand-name {
    font-family: "Montserrat", Arial, sans-serif; font-weight: 700; font-size: 22px;
    color: var(--teal-dark); letter-spacing: 1px; line-height: 1.1;
  }
  .headline-band { position: absolute; left: 0; top: 160px; }
  .headline {
    position: absolute; left: 40px; top: 182px; font-family: "Montserrat", Arial, sans-serif;
    color: var(--white); text-transform: uppercase; line-height: 1;
  }
  .headline .big { display: block; font-weight: 900; font-size: 46px; letter-spacing: 0.5px; }
  .headline .small { display: block; font-weight: 800; font-size: 27px; margin-top: 6px; }
  .intro {
    position: absolute; left: 40px; top: 370px; width: 340px;
    font-size: 13.5px; line-height: 1.6; color: var(--ink);
  }
  .experience { position: absolute; left: 40px; top: 530px; width: 350px; display: flex; gap: 16px; }
  .experience-seal {
    flex: 0 0 120px; height: 120px; border-radius: 50%;
    background: var(--white); border: 6px solid var(--teal); box-shadow: 0 0 0 3px var(--teal-dark) inset;
  }
  .experience-text { font-size: 13px; line-height: 1.55; color: var(--ink); }
  .meeting-photo {
    position: absolute; left: 40px; top: 700px; width: 340px; height: 200px;
    background: linear-gradient(135deg, #dfe7ea 0%, #b5c4cb 55%, #6f8590 100%);
    border-bottom: 6px solid var(--teal);
  }
  .services {
    position: absolute; left: 410px; top: 370px; width: 334px; height: 590px;
    background: linear-gradient(180deg, var(--teal-dark) 0%, var(--navy) 100%);
    padding: 34px 28px 0 28px; border-radius: 2px;
  }
  .services-title {
    font-family: "Montserrat", Arial, sans-serif; font-weight: 800; font-size: 26px;
    color: var(--white); letter-spacing: 1px; margin-bottom: 6px;
  }
  .services-rule { width: 60px; height: 4px; background: var(--teal-light); margin-bottom: 24px; }
  .service-list { list-style: none; }
  .service-item {
    display: flex; align-items: flex-start; gap: 12px; margin-bottom: 20px;
    font-family: "Montserrat", Arial, sans-serif; font-weight: 600; font-size: 14.5px;
    color: var(--white); line-height: 1.35;
  }
  .service-item svg { flex: 0 0 24px; margin-top: 1px; }
  .contact-list { position: absolute; left: 40px; top: 1000px; list-style: none; }
  .contact-item {
    display: flex; align-items: center; gap: 10px; margin-bottom: 14px;
    font-size: 13px; font-weight: 600; color: var(--teal-dark);
  }
  .contact-item svg { flex: 0 0 26px; }
  .call-box {
    position: absolute; left: 410px; top: 985px; width: 334px; height: 110px;
    background: var(--teal); padding: 18px 28px; color: var(--white);
    font-family: "Montserrat", Arial, sans-serif;
  }
  .call-box .call-label { font-weight: 800; font-size: 18px; letter-spacing: 1px; }
  .call-box .call-number { font-weight: 900; font-size: 30px; margin-top: 2px; }
  .call-box .call-address { font-weight: 600; font-size: 13px; margin-top: 6px; }
  .footer-band { position: absolute; left: 0; bottom: 0; }
</style>
</head>
<body>
<div class="flyer">

  <div class="hero-photo" role="img" aria-label="Photo of a businessman in a suit working at a laptop in a bright office"></div>
  <svg class="hero-frame" width="484" height="345" viewBox="0 0 484 345" aria-hidden="true">
    <polygon points="60,0 90,0 0,345 -30,345" fill="#d7dadb"/>
    <polygon points="104,0 118,0 28,345 14,345" fill="#9aa0a3"/>
    <polygon points="80,340 484,340 484,345 78,345" fill="#1b9ea6"/>
  </svg>

  <div class="brand">
    <span class="brand-mark"></span>
    <span class="brand-name">STEADY LEDGER<br>BOOKKEEPING</span>
  </div>

  <svg class="headline-band" width="440" height="190" viewBox="0 0 440 190" aria-hidden="true">
    <polygon points="0,0 440,0 400,170 0,170" fill="#1b9ea6"/>
    <polygon points="0,170 400,170 392,190 0,190" fill="#0e5a66"/>
  </svg>
  <h1 class="headline">
    <span class="big">Bookkeeping</span>
    <span class="big">Tailored</span>
    <span class="small">To Your Business Needs</span>
  </h1>

  <p class="intro">Are you a small business owner, tradie or TRPQ Service Provider struggling to stay on top of your bookkeeping and compliance obligations? If so we would love to help you get back on track and take control of your business finances so that you can make informed business decisions and focus on what you do best.</p>

  <div class="experience">
    <div class="experience-seal" aria-hidden="true"></div>
    <p class="experience-text">We have over 20 years industry experience and, as a small business ourselves, we are able to offer our clients a personal bookkeeping solution tailored to meet the needs of your business.</p>
  </div>

  <div class="meeting-photo" role="img" aria-label="Photo of a bookkeeper presenting charts to clients in a meeting room"></div>

  <section class="services">
    <h2 class="services-title">OUR SERVICES</h2>
    <div class="services-rule"></div>
    <ul class="service-list">
      <li class="service-item"><svg width="24" height="24" viewBox="0 0 24 24"><circle cx="12" cy="12" r="11" fill="#2bb7bd"/><path d="M7 12.5l3.2 3.2L17 8.8" fill="none" stroke="#fff" stroke-width="2.4" stroke-linecap="round" stroke-linejoin="round"/></svg>Accounts Payable | Accounts Receivable</li>
      <li class="service-item"><svg width="24" height="24" viewBox="0 0 24 24"><circle cx="12" cy="12" r="11" fill="#2bb7bd"/><path d="M7 12.5l3.2 3.2L17 8.8" fill="none" stroke="#fff" stroke-width="2.4" stroke-linecap="round" stroke-linejoin="round"/></svg>Customer Invoicing</li>
      <li class="service-item"><svg width="24" height="24" viewBox="0 0 24 24"><circle cx="12" cy="12" r="11" fill="#2bb7bd"/><path d="M7 12.5l3.2 3.2L17 8.8" fill="none" stroke="#fff" stroke-width="2.4" stroke-linecap="round" stroke-linejoin="round"/></svg>Bank and Credit Card Reconciliations</li>
      <li class="service-item"><svg width="24" height="24" viewBox="0 0 24 24"><circle cx="12" cy="12" r="11" fill="#2bb7bd"/><path d="M7 12.5l3.2 3.2L17 8.8" fill="none" stroke="#fff" stroke-width="2.4" stroke-linecap="round" stroke-linejoin="round"/></svg>Payroll | Superannuation | Payroll Tax</li>
      <li class="service-item"><svg width="24" height="24" viewBox="0 0 24 24"><circle cx="12" cy="12" r="11" fill="#2bb7bd"/><path d="M7 12.5l3.2 3.2L17 8.8" fill="none" stroke="#fff" stroke-width="2.4" stroke-linecap="round" stroke-linejoin="round"/></svg>Business Activity | Instalment Activity Statements</li>
      <li class="service-item"><svg width="24" height="24" viewBox="0 0 24 24"><circle cx="12" cy="12" r="11" fill="#2bb7bd"/><path d="M7 12.5l3.2 3.2L17 8.8" fill="none" stroke="#fff" stroke-width="2.4" stroke-linecap="round" stroke-linejoin="round"/></svg>Regular Financial Reports</li>
      <li class="service-item"><svg width="24" height="24" viewBox="0 0 24 24"><circle cx="12" cy="12" r="11" fill="#2bb7bd"/><path d="M7 12.5l3.2 3.2L17 8.8" fill="none" stroke="#fff" stroke-width="2.4" stroke-linecap="round" stroke-linejoin="round"/></svg>Vantly and Brimfolk Set-Up and Training</li>
    </ul>
  </section>

  <ul class="contact-list">
    <li class="contact-item"><svg width="26" height="26" viewBox="0 0 26 26"><circle cx="13" cy="13" r="12" fill="#1b9ea6"/><rect x="7" y="9" width="12" height="8" rx="1" fill="none" stroke="#fff" stroke-width="1.6"/><path d="M7 9.5l6 4.5 6-4.5" fill="none" stroke="#fff" stroke-width="1.6"/></svg>hello@steadyledger.example</li>
    <li class="contact-item"><svg width="26" height="26" viewBox="0 0 26 26"><circle cx="13" cy="13" r="12" fill="#1b9ea6"/><circle cx="13" cy="13" r="6" fill="none" stroke="#fff" stroke-width="1.6"/><path d="M7 13h12M13 7c-3 3.5-3 8.5 0 12M13 7c3 3.5 3 8.5 0 12" fill="none" stroke="#fff" stroke-width="1.3"/></svg>www.steadyledger.example</li>
  </ul>

  <div class="call-box">
    <div class="call-label">CALL US NOW</div>
    <div class="call-number">0400 612 738</div>
    <div class="call-address">PO Box 41 Northgate NSW 2700</div>
  </div>

  <svg class="footer-band" width="784" height="70" viewBox="0 0 784 70" aria-hidden="true">
    <polygon points="0,40 784,40 784,70 0,70" fill="#5d6265"/>
    <polygon points="420,40 784,40 784,70 400,70" fill="#0e5a66"/>
    <polygon points="0,32 300,32 290,40 0,40" fill="#1b9ea6"/>
  </svg>

</div>
</body>
</html>
```